Heritage Hollow Business Cards

Require a business card design. <br/><br/>Needs to include logo (either round or long version) plus these details:<br/>Maya Torvell<br/>Heritage Hollow<br/>maya@kelvadtrading.com.au<br/>02 6481 7395<br/>PO Box Glenwarra NSW 2791<br/>www.heritagehollow.com.au<br/><br/>I need in an editable format so that I can create for multiple staff members. <br/><br/>

Target Market(s)

We are an online store selling renovation products to home owners are builders. Looking for a classic classy design.

Industry/Entity Type

Home And Garden

Contact Information for Business Card

Maya Torvell
Heritage Hollow
maya@kelvadtrading.com.au
02 6481 7395
PO Box Glenwarra NSW 2791
www.heritagehollow.com.au

Colors

Designer to choose colors to be used in the design.

Requirements
Must have
• Must include Logo.

```html
<!DOCTYPE html>
<html lang="en">
<head>
<meta charset="utf-8">
<title>Heritage Hollow Business Cards</title>
<link href="https://fonts.googleapis.com/css2?family=Open+Sans:wght@400;600&family=Raleway:wght@400&display=swap" rel="stylesheet">
<style>
  :root {
    --backdrop: #c2c2c2;
    --card: #ffffff;
    --ink: #141518;
    --band: #131418;
    --accent: #557565;
    --rule: #4a4a4a;
  }
  * { margin: 0; padding: 0; box-sizing: border-box; }
  html, body { width: 978px; height: 1200px; overflow: hidden; }
  body {
    background: var(--backdrop);
    font-family: "Open Sans", sans-serif;
    color: var(--ink);
    position: relative;
  }
  .card {
    position: absolute;
    left: 206px;
    width: 576px;
    height: 329px;
    background: var(--card);
    border: 1px solid var(--ink);
    overflow: hidden;
    box-shadow: 0 26px 22px -18px rgba(0,0,0,0.35);
  }
  .card--front { top: 223px; }
  .card--back { top: 635px; }
  .band {
    position: absolute;
    left: 0; right: 0; bottom: 0;
    height: 73px;
    background: var(--band);
    color: #fff;
  }
  /* front */
  .front-brand {
    position: absolute;
    left: 70px; top: 80px;
    display: flex; align-items: center; gap: 16px;
  }
  .brand-dot {
    width: 70px; height: 70px;
    border: 1.5px solid var(--ink);
    border-radius: 50%;
  }
  .front-brand .brand-name {
    font-size: 44px; font-weight: 600; letter-spacing: 0.5px;
  }
  .front-url {
    text-align: center;
    line-height: 73px;
    font-size: 19px;
    letter-spacing: 3.2px;
    padding-top: 0;
    margin-top: -8px;
  }
  /* back */
  .back-brand {
    position: absolute;
    left: 42px; top: 23px;
    width: 208px; height: 208px;
    border: 1px solid var(--rule);
    border-radius: 50%;
    display: flex; align-items: center; justify-content: center;
    text-align: center;
  }
  .back-brand .brand-name {
    font-size: 27px; font-weight: 600; line-height: 1.05;
  }
  .divider {
    position: absolute;
    left: 285px; top: 0;
    width: 12px; height: 256px;
    background: var(--band);
  }
  .contact-list { list-style: none; }
  .contact-item {
    position: absolute;
    left: 271px;
    display: flex; align-items: center;
    height: 36px;
  }
  .contact-icon {
    width: 42px; height: 36px;
    background: var(--accent);
    display: flex; align-items: center; justify-content: center;
  }
  .contact-text {
    margin-left: 20px;
    font-size: 12.5px;
  }
  .person {
    padding: 13px 0 0 28px;
  }
  .person-name {
    font-family: "Raleway", sans-serif;
    font-size: 30px; letter-spacing: 1.5px; line-height: 1;
  }
  .person-role {
    font-family: "Raleway", sans-serif;
    font-size: 14px; margin-top: 2px;
  }
</style>
</head>
<body>

<section class="card card--front">
  <div class="front-brand">
    <span class="brand-dot"></span>
    <span class="brand-name">Heritage Hollow</span>
  </div>
  <div class="band">
    <p class="front-url">www.heritagehollow.com.au</p>
  </div>
</section>

<section class="card card--back">
  <div class="back-brand">
    <span class="brand-name">Heritage<br>Hollow</span>
  </div>
  <div class="divider"></div>
  <ul class="contact-list">
    <li class="contact-item" style="top:33px">
      <span class="contact-icon">
        <svg width="20" height="20" viewBox="0 0 24 24"><path fill="#fff" d="M6.6 10.8a15.1 15.1 0 0 0 6.6 6.6l2.2-2.2c.3-.3.7-.4 1-.2 1.1.4 2.3.6 3.6.6.6 0 1 .4 1 1V20c0 .6-.4 1-1 1A17 17 0 0 1 3 4c0-.6.4-1 1-1h3.5c.6 0 1 .4 1 1 0 1.3.2 2.5.6 3.6.1.3 0 .7-.2 1z"/></svg>
      </span>
      <span class="contact-text">02 6481 7395</span>
    </li>
    <li class="contact-item" style="top:83px">
      <span class="contact-icon">
        <svg width="22" height="16" viewBox="0 0 22 16"><rect x="1" y="1" width="20" height="14" fill="none" stroke="#fff" stroke-width="1.6"/><path d="M1 1l10 8 10-8M1 15l7-6M21 15l-7-6" fill="none" stroke="#fff" stroke-width="1.4"/></svg>
      </span>
      <span class="contact-text">maya@kelvadtrading.com.au</span>
    </li>
    <li class="contact-item" style="top:133px">
      <span class="contact-icon">
        <svg width="20" height="20" viewBox="0 0 20 20"><circle cx="10" cy="10" r="8.5" fill="none" stroke="#fff" stroke-width="1.6"/><path d="M2 10h16M10 1.5c-3 3-3 14 0 17M10 1.5c3 3 3 14 0 17" fill="none" stroke="#fff" stroke-width="1.2"/></svg>
      </span>
      <span class="contact-text">www.heritagehollow.com.au</span>
    </li>
    <li class="contact-item" style="top:186px">
      <span class="contact-icon">
        <svg width="16" height="22" viewBox="0 0 16 22"><path fill="#fff" d="M8 0a8 8 0 0 0-8 8c0 6 8 14 8 14s8-8 8-14a8 8 0 0 0-8-8zm0 11a3 3 0 1 1 0-6 3 3 0 0 1 0 6z"/></svg>
      </span>
      <span class="contact-text">PO Box Glenwarra NSW 2791</span>
    </li>
  </ul>
  <div class="band">
    <div class="person">
      <p class="person-name">MAYA TORVELL</p>
      <p class="person-role">Director</p>
    </div>
  </div>
</section>

</body>
</html>
```